Consulting company business cards

We have a base design, but would be willing to update. We have a new logo/"tag" that needs to be added. Current business card design is attached for reference into our "style."

Industry/Entity Type

Business

Contact Information for Business Card

Should contain name and title, office number, mobile number if appropriate, e-mail, website, physical address, and company logo.

Font styles to use
Other font styles liked:
• See current card design on KorvandBCard

Colors
0455a3
85acd3
aaaaaa

Requirements
Must have
• Our colors are navy blue, gray, and a lighter blue
Nice to have
• Design that I can easily drop in new names/titles as we hire employees.

```html
<!DOCTYPE html>
<html lang="en">
<head>
<meta charset="utf-8">
<title>Brantley Business Cards</title>
<link href="https://fonts.googleapis.com/css2?family=Open+Sans:wght@400;600;700&display=swap" rel="stylesheet">
<style>
  :root {
    --navy: #0b3150;
    --sky: #7badd0;
    --gray: #8a8a8a;
    --paper: #ffffff;
    --backdrop: #e6e8eb;
    --faint: #f1f2f3;
  }
  * { margin: 0; padding: 0; box-sizing: border-box; }
  html, body { width: 1200px; height: 900px; overflow: hidden; }
  body {
    position: relative;
    background: var(--backdrop);
    font-family: "Open Sans", Arial, sans-serif;
  }
  .card {
    position: absolute;
    background: var(--paper);
    overflow: hidden;
    box-shadow: 0 6px 20px rgba(0,0,0,.15);
  }
  .card--front { left: 77px; top: 33px; width: 590px; height: 365px; }
  .card--back { left: 388px; top: 505px; width: 566px; height: 353px; }

  .wordmark { display: flex; align-items: center; gap: 14px; }
  .wordmark__name {
    font-weight: 700;
    letter-spacing: 4px;
    line-height: 1;
  }
  .wordmark__dot { border-radius: 50%; flex: none; }
  .tagline {
    letter-spacing: 2.2px;
    text-transform: uppercase;
    font-weight: 400;
  }

  /* front */
  .front__brand { position: absolute; left: 33px; top: 30px; }
  .front__brand .wordmark__name { font-size: 58px; color: var(--navy); }
  .front__brand .wordmark__dot { width: 56px; height: 56px; background: var(--sky); }
  .front__brand .tagline { font-size: 14.5px; color: var(--gray); margin-top: 12px; }

  .front__band {
    position: absolute; left: 0; top: 157px; width: 100%; height: 208px;
    background: var(--navy);
  }
  .front__emblem {
    position: absolute; left: 388px; top: 145px; width: 202px; height: 220px;
    background: var(--sky);
    border-top-left-radius: 90px;
    border-bottom-left-radius: 30px;
  }
  .contact {
    position: absolute; left: 32px; top: 181px;
    color: var(--paper);
  }
  .contact__name { font-size: 21px; font-weight: 600; line-height: 1.2; }
  .contact__title { font-size: 15px; margin-top: 2px; }
  .contact__address { font-size: 15px; margin-top: 30px; }
  .contact__phones { font-size: 15px; margin-top: 14px; }
  .contact__web { font-size: 15px; margin-top: 6px; }
  .sep { margin: 0 16px; }

  /* back */
  .back__band {
    position: absolute; left: 0; top: 110px; width: 100%; height: 131px;
    background: var(--navy);
    display: flex; flex-direction: column; align-items: center; justify-content: center;
  }
  .back__band .wordmark__name { font-size: 44px; color: var(--paper); }
  .back__band .wordmark__dot { width: 42px; height: 42px; background: var(--paper); }
  .back__band .tagline { font-size: 13px; color: var(--paper); margin-top: 9px; }
  .back__watermark {
    position: absolute; left: 160px; top: 241px; width: 400px; height: 112px;
    background: var(--faint);
    border-top-left-radius: 60px;
  }
</style>
</head>
<body>
  <section class="card card--front">
    <div class="front__brand">
      <div class="wordmark">
        <span class="wordmark__name">BRANTLEY</span>
        <span class="wordmark__dot"></span>
      </div>
      <p class="tagline">A Cloud Consulting Company</p>
    </div>
    <div class="front__band"></div>
    <div class="front__emblem" role="img" aria-label="Large light blue brand mascot illustration"></div>
    <div class="contact">
      <p class="contact__name">Dana Korvand</p>
      <p class="contact__title">Office Manager</p>
      <p class="contact__address">1850 N Alder Ave Springfield Ohio 45501</p>
      <p class="contact__phones">555.014.2210<span class="sep">|</span>555.014.2271</p>
      <p class="contact__web">dkorvand@brantleytech.com<span class="sep" style="margin:0 8px">|</span>brantleytech.com</p>
    </div>
  </section>

  <section class="card card--back">
    <div class="back__band">
      <div class="wordmark">
        <span class="wordmark__name">BRANTLEY</span>
        <span class="wordmark__dot"></span>
      </div>
      <p class="tagline">A Cloud Consulting Company</p>
    </div>
    <div class="back__watermark" role="img" aria-label="Faint brand mascot decoration"></div>
  </section>
</body>
</html>
```